Building company buisness cards

We are looking for a sharp modern new look for our business cards.We are a New Zealand based company that specialises in house and land packages.We have attached a photo of the current logo and would like to see if it can be improved somehow if needed.We are open to any colours but we have chosen Black and White at this stage. Feel free to change the font and make the logo smarter looking.Play with the colours and see what looks best.We want a card that looks so good know one will want to throw it away!

Target Market(s)

Building profesonals, home buyers

Industry/Entity Type

Building

Contact Information for Business Card

Garrick Tenwood
0275390628
garrickt@hartvale.co.nz

Font styles to use
Serif
Sans Serif

Colors

Designer to choose colors to be used in the design.

Requirements
Must have
• Just the logo on one side and details on the other
• Clean simple looking card
Nice to have
• Round corners and detail like raised or spot UV
• Something that stands out
Should not have
• To title needed, Director etc

```html
<!DOCTYPE html>
<html lang="en">
<head>
<meta charset="utf-8">
<title>Hartvale Business Cards</title>
<link rel="stylesheet" href="https://fonts.googleapis.com/css2?family=Playfair+Display:wght@700&family=Libre+Caslon+Text&family=Montserrat:wght@400&display=swap">
<style>
  :root {
    --backdrop: #3b3431;
    --card-white: #f7f7f5;
    --card-black: #141414;
    --ink: #111114;
    --name-grey: #a9a9a9;
    --tagline: #2a2a30;
  }
  * { margin: 0; padding: 0; box-sizing: border-box; }
  html, body {
    width: 1200px;
    height: 844px;
    overflow: hidden;
    background: var(--backdrop);
  }
  .canvas {
    position: relative;
    width: 1200px;
    height: 844px;
  }
  .card {
    position: absolute;
    top: 269px;
    width: 500px;
    height: 306px;
    border-radius: 14px;
    box-shadow: 0 10px 30px rgba(0, 0, 0, 0.35);
  }
  .card--details {
    left: 70px;
    background: var(--card-white);
    color: var(--ink);
  }
  .card--brand {
    left: 630px;
    background: var(--card-black);
  }
  .company {
    position: absolute;
    font-family: "Libre Caslon Text", serif;
    font-weight: 400;
    line-height: 1;
    letter-spacing: 1px;
  }
  .card--details .company {
    left: 40px;
    top: 62px;
    font-size: 52px;
    color: var(--ink);
  }
  .tagline {
    position: absolute;
    left: 42px;
    top: 130px;
    font-family: "Montserrat", sans-serif;
    font-size: 14px;
    letter-spacing: 0.4px;
    color: var(--tagline);
  }
  .person {
    position: absolute;
    left: 40px;
    top: 178px;
    font-family: "Playfair Display", serif;
    font-weight: 700;
    font-size: 25px;
  }
  .contact {
    position: absolute;
    left: 40px;
    top: 230px;
    list-style: none;
    font-family: "Libre Caslon Text", serif;
    font-size: 16px;
    line-height: 23px;
  }
  .card--brand .company {
    left: 50%;
    top: 50%;
    transform: translate(-50%, -50%);
    font-size: 56px;
    color: var(--name-grey);
  }
</style>
</head>
<body>
<main class="canvas">
  <section class="card card--details" aria-label="Business card, details side">
    <p class="company">Hartvale</p>
    <p class="tagline">Homes shaped around you.</p>
    <h1 class="person">Garrick Tenwood</h1>
    <ul class="contact">
      <li>P: 0275390628</li>
      <li>E: garrickt@hartvale.co.nz</li>
    </ul>
  </section>

  <section class="card card--brand" aria-label="Business card, company name side">
    <p class="company">Hartvale</p>
  </section>
</main>
</body>
</html>
```